Business Card design project for new family-run construction business

We need a logo and business card designed for a new construction company. We want to convey a professional, but approachable image. We hope to be servicing small residential clients as well as large commercial contracts as well.
Our business will employ a single "Hydro excavator" truck, which can be used for multiple purposes: vacuuming up dirt or water, digging holes, clearing sewer blockages and so on.
We are open to different colour schemes, however blue and white, or yellow/green would be good combinations. We are open to multiple colours (2-4), so long as they are complimentary.

EDIT: Let's not put much emphasis on the octopus... unless it's very clear that the arms are actual vacuum hoses, it won't make sense. An octopus on it's own has little to do with our business.

Please also do not use actual photos of hydro-vac trucks. This is not the aesthetic we are going for.

**The logo should instead be: A stylized outline of a hydrovac truck (a line drawing or digital version of a line-drawing). See the two examples in the attached images of hydrovac trucks. I've also included a very crude pen outline as a reference. Please use your artistic discretion and talent (as I clearly have none) to make something that looks much nicer. Thanks for your efforts!**

The front of the card should have the following elements:
Logo
Name: R & T Hydro Excavation and Flushign
Two phone numbers: Direct and Office
Email address
Website
It should also have the name of the employee and their job title
At the bottom of the card it should say (in a noticeable way): "24/7 Emergency Calls Welcome"

The back of the card should have the following elements:
"20 Years Experience"
"A Canadian Family Run Business"
A small maple-leaf logo that is in a similar style to the rest of the card/logos in the bottom right corner of the back of the card. (see attached)

**We have just added a number of business card designs that really appeal to us to offer inspiration.**

Reason: We have not received designs that hit the mark of what we are looking for. Feedback has been posted, so we would like to provide the designers more time.

Target Market(s)

Commercial and residential customers. As big as large malls and office buildings, as small single-family home owners

Industry/Entity Type

Construction Company

Contact Information for Business Card

We have just added a number of business card designs that really appeal to us to offer inspiration.

Logo
Email address
Website

"20 Years Experience"

Logo Text

R & T Hydro Excavation and Flushing

Font styles to use
Serif
Sans Serif
Other font styles liked:
• Helvetica, Futura, Impact, bold strong, modern fonts that convey a sense of design and style

Colors
0592cd
ec1f27
9bcb3c

Requirements
Must have
• The front of the card should have the following elements:
• Logo
• Name: R & T Hydro Excavation and Flushign
• Two phone numbers: Direct and Office
• Email address
• Website
• It should also have the name of the employee and their job title
• At the bottom of the card it should say (in a noticeable way): "24/7 Emergency Calls Welcome"
• The back of the card should have the following elements:
• "20 Years Experience"
• "A Canadian Family Run Business"
• A small maple-leaf logo that is in a similar style to the rest of the card/logos in the bottom right corner of the back of the card. (see attached)
Nice to have
• The card does not have to be a perfect rectangle. We are open to rounded corners or cut out elements.
• Also embossing, engraving, adding highlighted/glossy layers (spot glass?), or any other effect that will give the card a unique look/feel is more than welcome.
• We would love to have a card that stands out from others and is compelling to look at it, so we are happy to incorporate any sort of modern printing technology to bring out the design.
• Please feel encouraged to be creative and design something unique, especially for this industry.
• Our dream would be if a Scandinavian architect were to go into the construction business and design this business card ;)
Should not have
• Photographs

```html
<!DOCTYPE html>
<html lang="en">
<head>
<meta charset="utf-8">
<title>R &amp; T Hydro Excavation and Flushing – Business Card</title>
<link rel="stylesheet" href="https://fonts.googleapis.com/css2?family=Arimo:wght@400&family=Questrial&display=swap">
<style>
  :root {
    --brand-red: #d21f27;
    --card-white: #ffffff;
    --stage-grey: #d6d6d6;
    --ink-dark: #2a2a2a;
    --ink-red: #d21f27;
  }
  * { box-sizing: border-box; margin: 0; padding: 0; }
  html, body { width: 1200px; height: 900px; overflow: hidden; }
  body {
    background: var(--stage-grey);
    font-family: "Questrial", "Century Gothic", sans-serif;
    position: relative;
  }
  .card {
    position: absolute;
    top: 300px;
    width: 525px;
    height: 300px;
    border-radius: 22px;
    overflow: hidden;
    box-shadow: 0 10px 28px rgba(0,0,0,0.18);
  }

  /* Back of card */
  .card-back {
    left: 45px;
    background: var(--brand-red);
    color: var(--card-white);
  }
  .back-headline {
    position: absolute;
    top: 118px;
    left: 0; right: 0;
    text-align: center;
    font-size: 21px;
    letter-spacing: 3px;
    text-transform: uppercase;
  }
  .back-tagline {
    position: absolute;
    top: 160px;
    left: 0; right: 0;
    text-align: center;
    font-size: 14.5px;
    letter-spacing: 2.6px;
    text-transform: uppercase;
  }
  .back-badge {
    position: absolute;
    right: 32px;
    bottom: 30px;
    width: 36px;
    height: 36px;
  }

  /* Front of card */
  .card-front {
    left: 630px;
    background: var(--card-white);
  }
  .company-name {
    position: absolute;
    left: 28px;
    top: 112px;
    width: 230px;
    color: var(--ink-red);
    font-size: 24px;
    line-height: 1.15;
    text-transform: uppercase;
    letter-spacing: 0.5px;
  }
  .divider {
    position: absolute;
    left: 280px;
    top: 82px;
    width: 1.5px;
    height: 152px;
    background: var(--brand-red);
  }
  .contact {
    position: absolute;
    left: 298px;
    top: 88px;
    font-family: "Arimo", Arial, sans-serif;
  }
  .person-name {
    font-size: 16px;
    color: var(--ink-dark);
  }
  .person-title {
    font-size: 11px;
    color: var(--ink-dark);
    margin-top: 4px;
  }
  .contact-list {
    list-style: none;
    margin-top: 26px;
    color: var(--ink-red);
    font-size: 12px;
    line-height: 15px;
  }
  .contact-list li {
    display: flex;
    align-items: center;
    gap: 4px;
  }
  .contact-list svg { width: 11px; height: 11px; flex: none; }
  .emergency-rule {
    position: absolute;
    left: 0; right: 0;
    top: 244px;
    height: 1px;
    background: var(--brand-red);
  }
  .emergency-band {
    position: absolute;
    left: 0; right: 0;
    top: 250px;
    height: 17px;
    background: var(--brand-red);
    color: var(--card-white);
    font-size: 10px;
    line-height: 17px;
    letter-spacing: 10px;
    text-align: center;
    text-transform: uppercase;
    font-family: "Arimo", Arial, sans-serif;
  }
</style>
</head>
<body>

  <section class="card card-back" aria-label="Back of business card">
    <p class="back-headline">20 Years Experience</p>
    <p class="back-tagline">A Canadian Family Run Business</p>
    <svg class="back-badge" viewBox="0 0 36 36" role="img" aria-label="Maple leaf badge">
      <circle cx="18" cy="18" r="16" fill="none" stroke="var(--card-white)" stroke-width="2.5"/>
      <circle cx="18" cy="18" r="10" fill="var(--card-white)"/>
    </svg>
  </section>

  <section class="card card-front" aria-label="Front of business card">
    <h1 class="company-name">R &amp; T Hydro Excavation and Flushing</h1>
    <div class="divider"></div>
    <div class="contact">
      <p class="person-name">Dana Korver</p>
      <p class="person-title">Manager</p>
      <ul class="contact-list">
        <li>
          <svg viewBox="0 0 12 12" aria-hidden="true"><rect x="3" y="0.8" width="6" height="10.4" rx="1" fill="none" stroke="currentColor" stroke-width="1.2"/><rect x="5" y="9" width="2" height="1" fill="currentColor"/></svg>
          555-631-0190
        </li>
        <li>
          <svg viewBox="0 0 12 12" aria-hidden="true"><path d="M2.5 1 L4.5 1 L5.3 3.6 L4 4.6 Q5 7 7.4 8 L8.4 6.7 L11 7.5 L11 9.5 Q10.5 11 9 11 Q1 10 1 3 Q1 1.5 2.5 1 Z" fill="currentColor"/></svg>
          555-631-0142
        </li>
        <li>
          <svg viewBox="0 0 12 12" aria-hidden="true"><rect x="0.8" y="2.5" width="10.4" height="7" rx="0.8" fill="none" stroke="currentColor" stroke-width="1.2"/><path d="M1 3 L6 6.8 L11 3" fill="none" stroke="currentColor" stroke-width="1.2"/></svg>
          dana@rthydroflush.com
        </li>
        <li>
          <svg viewBox="0 0 12 12" aria-hidden="true"><circle cx="6" cy="6" r="5.2" fill="none" stroke="currentColor" stroke-width="1.1"/><ellipse cx="6" cy="6" rx="2.2" ry="5.2" fill="none" stroke="currentColor" stroke-width="1"/><path d="M1 6 H11 M2 3.5 H10 M2 8.5 H10" stroke="currentColor" stroke-width="0.9"/></svg>
          rthydroflush.com
        </li>
      </ul>
    </div>
    <div class="emergency-rule"></div>
    <p class="emergency-band">24/7 Emergency Calls Welcome</p>
  </section>

</body>
</html>
```